Emerging automotive detailing business

I am starting a small automotive detailing business in hopes of becoming a well-known detailer to work on high end cars. I would like a card to reflect the high quality and time I put into my work. The name of the company is Bright Crest Detailing. I feel like it represents racecars getting off the line at the drag strip as well as an innuendo of "Up the Ladder". I do minor paint correction such as clay barring, multi-step buffing and polishing, waxing, hand washes, etc. I am always striving to learn more and improve my work. My goal is to have total customer satisfaction. This is a female run business but I do not want it to be very girly. Elegant is okay! I have pictures of my personal wrenfield attached, they do not need to be incorporated but if you can think of a cool way to use 1 or all of them, go for it!

Target Market(s)

Anyone that owns a vehicle. Preferably high end vehicles such as Valtori, Castellverde and Morvani but I will also happily work on any car, truck or suv no matter what brand.

Industry/Entity Type

Automotive

Contact Information for Business Card

Bright Crest Detailing
Mira Tolland
4175 Quenhollow Rd
Ashmere PA 17492
Cell phone- call/text- 717-555-0148
email- brightcrestdetails@maildrop-example.com
Instagram: @brightcrestdetailing
Facebook: facebook.com/brightcrestdetailing

Requirements
Must have
• Business name, my name, address, phone number. Listing that I do minor paint correction such as clay barring, multi-step buffing and polishing, waxing, hand washes, interior cleaning, and more. (This last part was in nice to haves but I have realized that I do really want it, so I moved it to must haves.) I want something that is different and eye-catching to my customers. Some people have done this very well with cards already submitted to me, but a lot have not. I didn't mess with the "look and feel bars" much because because I am pretty open to the overall design as long as it is not your basic run of the mill design.
Nice to have
• Something car related. Maybe an appointment time/date line. I do not have a logo, but if you would like to design one and incorporate it, that would be amazing!
Should not have
• Purple and Pink colors. Boring, basic, normal card.

```html
<!DOCTYPE html>
<html lang="en">
<head>
<meta charset="utf-8">
<title>Bright Crest Detailing – Business Card</title>
<link rel="stylesheet" href="https://fonts.googleapis.com/css2?family=Arimo:wght@400&family=Libre+Baskerville:wght@400&display=swap">
<style>
  :root {
    --page: #e9e7e4;
    --paper: #ffffff;
    --paper-shade: #f1f1f1;
    --band: #2f3032;
    --band-text: #cfd0d2;
    --ink: #1d1d1d;
    --ink-soft: #3a3a3a;
    --night: #050505;
    --night-text: #e8e8e8;
    --rule-blue: #2d4ea8;
    --icon: #d9d9d9;
  }
  * { box-sizing: border-box; margin: 0; padding: 0; }
  html, body {
    width: 1200px; height: 902px; overflow: hidden;
    background: var(--page);
  }
  .canvas { position: relative; width: 1200px; height: 902px; }
  .card {
    position: absolute; left: 320px; width: 560px; height: 320px;
    overflow: hidden;
    box-shadow: 0 6px 18px rgba(0,0,0,0.18);
  }

  /* Front */
  .card--front { top: 100px; background: linear-gradient(180deg, var(--paper), var(--paper-shade)); }
  .front__band {
    position: absolute; top: 0; right: 0; width: 150px; height: 100%;
    background: var(--band);
    display: flex; flex-direction: column; justify-content: center;
    padding: 0 16px;
  }
  .services__label {
    font-family: Arimo, Arial, sans-serif; font-weight: 400;
    font-size: 10px; letter-spacing: 1.6px; text-transform: uppercase;
    color: var(--night-text);
    padding-bottom: 8px; margin-bottom: 10px;
    border-bottom: 1px solid var(--rule-blue);
  }
  .services {
    list-style: none;
    font-family: Arimo, Arial, sans-serif; font-weight: 400;
    font-size: 11.5px; line-height: 21px; color: var(--band-text);
  }
  .front__title {
    position: absolute; left: 0; top: 96px; width: 410px; text-align: center;
    font-family: "Libre Baskerville", Georgia, serif; font-weight: 400;
    font-size: 27px; color: var(--ink);
  }
  .front__name {
    position: absolute; left: 0; top: 138px; width: 410px; text-align: center;
    font-family: Arimo, Arial, sans-serif; font-weight: 400;
    font-size: 20px; color: var(--ink-soft);
  }
  .front__rule {
    position: absolute; left: 0; top: 268px; width: 410px; height: 1px;
    background: var(--ink-soft);
  }
  .front__pin { position: absolute; left: 58px; top: 241px; width: 18px; height: 28px; }
  .front__address {
    position: absolute; left: 92px; top: 244px;
    font-family: Arimo, Arial, sans-serif; font-weight: 400;
    font-size: 13px; color: var(--ink-soft); letter-spacing: 0.3px;
  }

  /* Back */
  .card--back { top: 482px; background: var(--night); }
  .back__title {
    position: absolute; left: 0; top: 62px; width: 100%; text-align: center;
    font-family: Arimo, Arial, sans-serif; font-weight: 400;
    font-size: 29px; color: var(--night-text);
  }
  .back__rule { position: absolute; left: 0; width: 100%; height: 2px; background: var(--rule-blue); }
  .back__rule--upper { top: 140px; }
  .back__rule--lower { top: 292px; }
  .back__name {
    position: absolute; left: 34px; top: 232px;
    font-family: Arimo, Arial, sans-serif; font-weight: 400;
    font-size: 25px; color: var(--night-text);
  }
  .contact-list {
    position: absolute; left: 282px; top: 166px; list-style: none;
    font-family: Arimo, Arial, sans-serif; font-weight: 400;
    font-size: 12.5px; color: var(--night-text);
  }
  .contact-list li { display: flex; align-items: center; gap: 8px; height: 24px; white-space: nowrap; }
  .contact-list svg { width: 12px; height: 12px; flex: none; }
</style>
</head>
<body>
<main class="canvas">

  <section class="card card--front" aria-label="Card front">
    <aside class="front__band" aria-label="Services">
      <p class="services__label">Paint Correction</p>
      <ul class="services">
        <li>Clay Barring</li>
        <li>Multi-Step Buffing</li>
        <li>Polishing</li>
        <li>Waxing</li>
        <li>Hand Washes</li>
        <li>Interior Cleaning</li>
        <li>&amp; More</li>
      </ul>
    </aside>
    <h1 class="front__title">Bright Crest Detailing</h1>
    <p class="front__name">Mira Tolland</p>
    <div class="front__rule"></div>
    <svg class="front__pin" viewBox="0 0 18 28" aria-hidden="true">
      <path d="M9 1C4.6 1 1 4.5 1 8.9 1 14.5 9 27 9 27s8-12.5 8-18.1C17 4.5 13.4 1 9 1z" fill="#ffffff" stroke="#2a2a2a" stroke-width="2"/>
      <circle cx="9" cy="9" r="3" fill="#2a2a2a"/>
    </svg>
    <p class="front__address">4175 Quenhollow Rd, Ashmere PA 17492</p>
  </section>

  <section class="card card--back" aria-label="Card back">
    <h2 class="back__title">Bright Crest Detailing</h2>
    <div class="back__rule back__rule--upper"></div>
    <div class="back__rule back__rule--lower"></div>
    <p class="back__name">Mira Tolland</p>
    <ul class="contact-list">
      <li>
        <svg viewBox="0 0 12 12" aria-hidden="true"><rect width="12" height="12" rx="1" fill="var(--icon)"/><rect x="4" y="2" width="4" height="8" rx="0.8" fill="#050505"/></svg>
        717-555-0148
      </li>
      <li>
        <svg viewBox="0 0 12 12" aria-hidden="true"><rect width="12" height="12" rx="1" fill="var(--icon)"/></svg>
        @brightcrestdetailing
      </li>
      <li>
        <svg viewBox="0 0 12 12" aria-hidden="true"><rect width="12" height="12" rx="1" fill="var(--icon)"/><rect x="2.5" y="3.5" width="7" height="5" fill="none" stroke="#050505" stroke-width="1"/><path d="M2.5 3.5 6 6.5 9.5 3.5" fill="none" stroke="#050505" stroke-width="1"/></svg>
        brightcrestdetails@maildrop-example.com
      </li>
      <li>
        <svg viewBox="0 0 12 12" aria-hidden="true"><rect width="12" height="12" rx="1" fill="var(--icon)"/><path d="M6 2.2C4.5 2.2 3.4 3.3 3.4 4.7 3.4 6.6 6 9.8 6 9.8s2.6-3.2 2.6-5.1C8.6 3.3 7.5 2.2 6 2.2z" fill="#050505"/></svg>
        4175 Quenhollow Rd, Ashmere PA 17492
      </li>
    </ul>
  </section>

</main>
</body>
</html>
```